Business Card Design for company

We want new business cards. We'd like something different-- yet still highly professional. Our tagline is Providing leadership, delivering success. Stock photos are ok, as long as they are relevant and look upscale.

Target Market(s)

Architecture/Business Management Consulting/Engineering Consulting

Contact Information for Business Card

dark gray background with pops of blue might be good, but you tell me. You're the designers. Rounded corners might be nice, but again, you tell me.

Font styles to use
Serif
Sans Serif

Colors
3276b5
5c5c5c
9d9d9d
fbfbfb

Requirements
Nice to have
• Something different, but still very professional.

```html
<!DOCTYPE html>
<html lang="en">
<head>
<meta charset="utf-8">
<title>Veyra Global Business Cards</title>
<link rel="stylesheet" href="https://fonts.googleapis.com/css2?family=Mulish:wght@400;500;800&display=swap">
<style>
  :root {
    --page-bg: #cdcbcc;
    --card-white: #fbfbfb;
    --brand-blue: #286193;
    --ink-dark: #45484d;
    --ink-body: #3c3f44;
    --on-blue: #ffffff;
  }
  * { margin: 0; padding: 0; box-sizing: border-box; }
  html, body { width: 1200px; height: 1050px; overflow: hidden; }
  body {
    position: relative;
    background: var(--page-bg);
    font-family: "Mulish", Arial, sans-serif;
  }
  .card {
    position: absolute;
    left: 256px;
    width: 690px;
    border-radius: 32px;
  }
  .card--front { top: 102px; height: 395px; background: var(--card-white); }
  .card--back  { top: 555px; height: 393px; background: var(--brand-blue); }

  .front-brand {
    position: absolute;
    left: 370px; top: 120px;
    font-size: 38px; font-weight: 800;
    color: var(--brand-blue);
    letter-spacing: 0.5px;
    line-height: 1;
  }
  .front-address {
    position: absolute;
    left: 368px; top: 214px;
    font-size: 18px; line-height: 22px;
    color: var(--ink-body);
    letter-spacing: 0.4px;
  }
  .front-rule {
    position: absolute;
    left: 368px; top: 272px;
    width: 259px; height: 2px;
    background: var(--brand-blue);
  }
  .contact-list {
    position: absolute;
    left: 368px; top: 285px;
    list-style: none;
    font-size: 18px; line-height: 22.5px;
    color: var(--ink-body);
    letter-spacing: 0.3px;
  }
  .contact-list li { display: flex; align-items: center; gap: 7px; }
  .contact-list svg { width: 14px; height: 14px; flex: none; }

  .person {
    position: absolute;
    left: 56px; top: 286px;
  }
  .person__name {
    font-size: 23px; font-weight: 800;
    color: var(--brand-blue);
    letter-spacing: 0.8px;
    line-height: 28px;
  }
  .person__role {
    font-size: 18px; color: var(--ink-body);
    line-height: 22px; letter-spacing: 0.3px;
  }

  .back-brand {
    position: absolute;
    left: 0; right: 0; top: 130px;
    text-align: center;
    font-size: 58px; font-weight: 800;
    color: var(--on-blue);
    letter-spacing: 1px;
    line-height: 1;
  }
  .back-rule {
    position: absolute;
    left: 329px; top: 316px;
    width: 33px; height: 3px;
    background: var(--on-blue);
  }
  .back-web {
    position: absolute;
    left: 0; right: 0; top: 330px;
    text-align: center;
    font-size: 18px; color: var(--on-blue);
    letter-spacing: 0.4px;
  }
</style>
</head>
<body>
  <section class="card card--front">
    <div class="front-brand">Veyra Global</div>
    <p class="front-address">220 W. Alder St Suite 410<br>Mesa, AZ 85201</p>
    <div class="front-rule"></div>
    <ul class="contact-list">
      <li>
        <svg viewBox="0 0 24 24" aria-hidden="true"><path fill="#286193" d="M6.6 10.8a15.1 15.1 0 0 0 6.6 6.6l2.2-2.2a1 1 0 0 1 1-.25 11.4 11.4 0 0 0 3.6.57 1 1 0 0 1 1 1V20a1 1 0 0 1-1 1A17 17 0 0 1 3 4a1 1 0 0 1 1-1h3.5a1 1 0 0 1 1 1c0 1.25.2 2.45.57 3.57a1 1 0 0 1-.25 1z"/></svg>
        (555) 013.246
      </li>
      <li>
        <svg viewBox="0 0 24 24" aria-hidden="true"><rect x="2.5" y="5" width="19" height="14" fill="none" stroke="#286193" stroke-width="2"/><path d="M3 6l9 7 9-7" fill="none" stroke="#286193" stroke-width="2"/></svg>
        info@veyraglobal.com
      </li>
      <li>
        <svg viewBox="0 0 24 24" aria-hidden="true"><circle cx="12" cy="12" r="9.5" fill="none" stroke="#286193" stroke-width="2"/><path d="M2.5 12h19M12 2.5c3 3 3 16 0 19M12 2.5c-3 3-3 16 0 19" fill="none" stroke="#286193" stroke-width="1.8"/></svg>
        www.veyraglobal.com
      </li>
    </ul>
    <div class="person">
      <p class="person__name">DANIEL HARROW</p>
      <p class="person__role">CEO &amp; Founder</p>
    </div>
  </section>

  <section class="card card--back">
    <div class="back-brand">Veyra Global</div>
    <div class="back-rule"></div>
    <p class="back-web">www.veyraglobal.com</p>
  </section>
</body>
</html>
```